Büroausstattung Steuerberater
Alles prima. Frau Kestel arbeitet äußerst professionell und wird von uns auch zukünftig für anstehende Arbeiten beauftragt!
Zielgruppe
Typisch Steuerberater: Vom jungen Existenzgründer bis zum Geschäftsführer eines großen Unternehmens.
Mit anderen Worten: Nicht verspielt, aber auch nicht zu bieder.
Aufgabenstellung
Wir benötigen:
-Allg. Briefpapier
-Rechnungsvorlage (mit einfacher Excel-Addition)
-Faxvorlage
-Visitenkarten
-Memo Block (DIN A4 - kariert)
Wichtig:
Wir benötigen nicht nur einen Designvorschlag, sondern fertige Word bzw. Excel Dokumente, mit denen wir direkt arbeiten bzw. diese ausdrucken können!
Da wir bereits ein Logo haben, ist die Kreierung eines Logos nicht erforderlich.

```html
<!DOCTYPE html>
<html lang="de">
<head>
<meta charset="utf-8">
<title>Büroausstattung Steuerberater – Jens Wohlrath</title>
<link rel="stylesheet" href="https://fonts.googleapis.com/css2?family=Open+Sans:wght@400;600&display=swap">
<style>
  :root {
    --stage: #d9d9d9;
    --paper: #ffffff;
    --ink: #111111;
    --brand: #2c4a9c;
    --band-light: #b0c8ea;
    --band-mid: #6d88c8;
    --band-dark: #2d4595;
    --photo-a: #2f4f78;
    --photo-b: #9fb4c8;
  }
  * { box-sizing: border-box; margin: 0; padding: 0; }
  html, body { width: 1200px; height: 914px; overflow: hidden; }
  body {
    background: var(--stage);
    font-family: "Open Sans", Verdana, sans-serif;
    color: var(--ink);
    position: relative;
  }
  .sheet, .card { position: absolute; background: var(--paper); border: 1px solid #222; overflow: hidden; }
  .label { position: absolute; font-size: 12px; color: #111; }

  /* Colour band: one soft gradient in the brand blues */
  .band {
    position: absolute;
    background: linear-gradient(90deg, var(--band-light), var(--band-mid) 55%, var(--band-dark));
  }
  .band-photo {
    background: linear-gradient(90deg, var(--band-light) 0%, var(--photo-b) 30%, var(--photo-a) 55%, var(--band-dark) 100%);
  }

  /* Wordmark */
  .wordmark { position: absolute; color: var(--brand); font-weight: 400; white-space: nowrap; display: flex; align-items: center; }
  .wordmark .dot { display: inline-block; background: var(--brand); margin-left: 8px; }

  .right { text-align: right; }

  /* Letter */
  .sheet { left: 30px; top: 33px; width: 600px; height: 850px; font-size: 9px; line-height: 11.3px; letter-spacing: 0.15px; }
  .sheet .band-top { left: 360px; top: 0; width: 240px; height: 28px; }
  .sheet .wordmark { left: 360px; top: 58px; font-size: 19px; letter-spacing: 0.5px; }
  .sheet .wordmark .dot { width: 14px; height: 14px; }
  .sender-line { position: absolute; left: 58px; top: 128px; color: var(--brand); }
  .contact-col { position: absolute; right: 66px; top: 128px; color: var(--brand); }
  .contact-col p + p { margin-top: 11px; }
  .recipient { position: absolute; left: 72px; top: 160px; font-style: normal; }
  .fold { position: absolute; left: 0; width: 9px; border-top: 1px solid #333; }
  .subject { position: absolute; left: 72px; top: 298px; }
  .salutation { position: absolute; left: 72px; top: 327px; }
  .body-text { position: absolute; left: 72px; top: 357px; width: 402px; text-align: justify; font-size: 9.4px; letter-spacing: 0.3px; }
  .body-text p + p { margin-top: 11px; }
  .closing { position: absolute; left: 72px; top: 652px; }
  .closing p + p { margin-top: 10px; }
  .footer-col { position: absolute; right: 66px; top: 658px; color: var(--brand); }
  .footer-col .gap { margin-top: 16px; }
  .sheet .band-bottom { left: 360px; bottom: 0; width: 240px; height: 57px; }

  /* Cards */
  .card { width: 243px; height: 157px; }
  .card-front { left: 687px; top: 170px; }
  .card-front .wordmark { left: 16px; top: 50px; font-size: 17px; letter-spacing: 0.4px; }
  .card-front .wordmark .dot { width: 12px; height: 12px; }
  .card-front .band { left: 0; bottom: 0; width: 243px; height: 54px; }

  .card-back { left: 839px; top: 362px; font-size: 8.4px; line-height: 10.4px; color: var(--brand); }
  .card-back .name { position: absolute; left: 34px; top: 22px; font-size: 11px; font-weight: 600; }
  .card-back .title { position: absolute; left: 34px; top: 36px; }
  .card-back .addr { position: absolute; left: 34px; top: 56px; }
  .card-back .tel { position: absolute; left: 34px; top: 85px; }
  .card-back .mark { position: absolute; right: 22px; top: 58px; width: 14px; height: 14px; background: var(--brand); }
  .card-back .band { left: 0; bottom: 0; width: 243px; height: 14px; }
</style>
</head>
<body>

  <!-- Geschäftsbrief -->
  <section class="sheet" aria-label="Geschäftsbrief">
    <div class="band band-top"></div>
    <div class="wordmark">Jens Wohlrath<span class="dot"></span></div>

    <p class="sender-line">Jens Wohlrath &nbsp;I&nbsp; Seeuferweg 17 B &nbsp;I&nbsp; 78462 Seebrück</p>

    <div class="contact-col right">
      <p>Dipl.Kaufmann / Steuerberater<br>Jens Wohlrath</p>
      <p>Seeuferweg 17 B<br>78462 Seebrück</p>
      <p>Telefon: +49 (0)7622-504318<br>Fax: +49 (0)7622-504319<br>E-Mail: info@wohlrath-steuer.eu<br>www.wohlrath-steuer.eu</p>
    </div>

    <address class="recipient">
      Herr<br>Max Mustermann<br>Postfach 12 34<br>Musterstraße 56<br><br>78910 Musterstadt
    </address>

    <span class="fold" style="top:251px"></span>
    <span class="fold" style="top:357px"></span>
    <span class="fold" style="top:507px"></span>

    <p class="subject">Mustertext als Blindtext gesetzt für Betreffzeile</p>
    <p class="salutation">Sehr geehrter Herr Mustermann</p>

    <div class="body-text">
      <p>Auch gibt es niemanden, der den Schmerz an sich liebt, sucht oder wünscht, nur, weil er Schmerz ist, es sei denn, es kommt zu zufälligen Umständen, in denen Mühen und Schmerz ihm große Freude bereiten können. Um ein triviales Beispiel zu nehmen, wer von uns unterzieht sich je anstrengender körperlicher Betätigung, außer um Vorteile daraus zu ziehen? Aber wer hat irgend ein Recht, einen Menschen zu tadeln, der die Entscheidung trifft, eine Freude zu genießen, die keine unangenehmen Folgen hat, oder einen, der Schmerz vermeidet, welcher keine daraus resultierende Freude nach sich zieht? Auch gibt es niemanden, der den Schmerz an sich liebt, sucht oder wünscht, nur, weil er Schmerz ist, es sei denn, es kommt zu zufälligen Umständen, in denen Mühen und Schmerz ihm große Freude bereiten können. Um ein triviales Beispiel zu nehmen, wer von uns unterzieht sich je anstrengender körperlicher Betätigung, außer um Vorteile daraus zu ziehen? Aber wer hat irgend ein Recht, einen Menschen zu tadeln, der die Entscheidung trifft, eine Freude zu genießen, die keine unangenehmen Folgen hat, oder einen, der Schmerz vermeidet, welcher keine daraus resultierende Freude nach sich zieht? Auch gibt es niemanden, der den Schmerz an sich liebt, sucht oder wünscht, nur,</p>
      <p>Auch gibt es niemanden, der den Schmerz an sich liebt, sucht oder wünscht, nur, weil er Schmerz ist, es sei denn, es kommt zu zufälligen Umständen, in denen Mühen und Schmerz ihm große Freude bereiten können. Um ein triviales Beispiel zu nehmen, wer von uns unterzieht sich je anstrengender körperlicher Betätigung, außer um Vorteile daraus zu ziehen? Aber wer hat irgend ein Recht, einen Menschen zu tadeln, der die Entscheidung trifft, eine Freude zu genießen, die keine unangenehmen Folgen hat, oder einen, der Schmerz vermeidet, welcher keine daraus resultierende Freude nach sich zieht? Auch gibt es niemanden, der den Schmerz an sich liebt.</p>
    </div>

    <div class="closing">
      <p>Mit freundlichen Grüßen</p>
      <p>Jens Wohlrath</p>
    </div>

    <div class="footer-col right">
      <p>Bankverbindung:</p>
      <p style="margin-top:4px">Kontonummer:<br>123 456 7789<br>Bankleitzahl:<br>123 1234</p>
      <p class="gap" style="margin-top:18px">St.Nr. 04318/07715</p>
      <p class="gap">Gerichtsstand:<br>Seebrück</p>
    </div>

    <div class="band band-photo band-bottom" role="img" aria-label="Farbband mit Segelbootmotiv auf dem Wasser"></div>
  </section>
  <p class="label" style="left:545px; top:886px;">Geschäftsbrief</p>

  <!-- Visitenkarte vorne -->
  <p class="label" style="left:818px; top:146px;">Visitenkarte vorne</p>
  <section class="card card-front" aria-label="Visitenkarte Vorderseite">
    <div class="wordmark">Jens Wohlrath<span class="dot"></span></div>
    <div class="band band-photo" role="img" aria-label="Farbband mit Segelbootmotiv auf dem Wasser"></div>
  </section>

  <!-- Visitenkarte hinten -->
  <p class="label" style="left:968px; top:340px;">Visitenkarte hinten</p>
  <section class="card card-back" aria-label="Visitenkarte Rückseite">
    <p class="name">Jens Wohlrath</p>
    <p class="title">Dipl.Kaufmann / Steuerberater</p>
    <p class="addr">Seeuferweg 17 B<br>78462 Seebrück</p>
    <p class="tel">Telefon:&nbsp;&nbsp;+49 (0)7622-504318<br>Fax:&nbsp;&nbsp;&nbsp;&nbsp;&nbsp;&nbsp;&nbsp;&nbsp;+49 (0)7622-504319<br>E-Mail: info@wohlrath-steuer.eu<br>Site: www.wohlrath-steuer.eu</p>
    <span class="mark"></span>
    <div class="band"></div>
  </section>

</body>
</html>
```